Website Widget/Code Snippet Website

We create a number of website plugins (called widgets) for a website builder called LumaSite. It is a library of widgets that users who design their site in LumaSite can use on their website.
I am looking for a new design for this site;
https://www.quillpatchery.net
The website is going to official launch so I would like a new, clean design that emphasizes the huge library of widgets for LumaSite.
Tag Line: QuillPatchery Makes Anything Possible
We should emphasize the Sign Up option which provides a subscription to access the widgets.
I would like;
1. A home page
2. A widgets page which shows all the available widgets
3. A pricing/signup page
4. Widget information page
One overall simplistic design that is easy to navigate
Industry/Entity Type
Website building and website design
Number of Pages Required
4 page
Look and feel

```html
<!DOCTYPE html>
<html lang="en">
<head>
<meta charset="utf-8">
<title>QuillPatchery — Widgets for LumaSite</title>
<link href="https://fonts.googleapis.com/css2?family=Rubik:wght@400;500;600&family=Roboto:wght@400;500;700&display=swap" rel="stylesheet">
<style>
:root{
  --navy:#0e1422;
  --navy-2:#161d2e;
  --blue:#1db9f0;
  --grey-band:#d9d9d9;
  --text:#1b1f29;
  --muted:#7c828d;
  --white:#ffffff;
  --card-dark:rgba(255,255,255,.07);
}
*{box-sizing:border-box;margin:0;padding:0}
html,body{width:1200px;height:4792px;overflow:hidden}
body{font-family:"Roboto",sans-serif;color:var(--text);background:var(--white)}
h1,h2,h3,h4,.nav a,.btn,.kicker{font-family:"Rubik",sans-serif}
section,header,footer{position:relative;width:1200px}
.abs{position:absolute}
.btn{display:inline-block;background:var(--blue);color:var(--white);font-size:13px;font-weight:500;text-transform:uppercase;text-align:center;line-height:48px;border-radius:3px;text-decoration:none}
.kicker{color:var(--blue);font-size:17px;font-weight:500;text-transform:uppercase;display:flex;align-items:center;gap:14px;letter-spacing:.5px}
.kicker::before,.kicker.center::after{content:"";width:28px;height:2px;background:var(--blue)}
.kicker.center{justify-content:center}
.section-title{font-size:43px;font-weight:500;text-transform:uppercase;text-align:center;letter-spacing:.5px}
.slant{position:absolute;left:0;width:1200px;display:block}

/* header */
.site-header{height:93px;background:var(--navy);display:flex;align-items:center;padding:0 112px}
.logo{display:flex;align-items:center;gap:12px;color:var(--blue);font-family:"Rubik",sans-serif;font-size:30px;font-weight:400;text-decoration:none}
.logo-mark{width:28px;height:28px;border:3px solid var(--blue);border-radius:5px}
.nav{margin-left:auto;display:flex;align-items:center;gap:30px}
.nav a{color:var(--white);font-size:13px;font-weight:500;text-transform:uppercase;text-decoration:none}
.nav a.active{color:var(--blue);border-bottom:2px solid var(--blue);padding-bottom:6px;margin-top:8px}
.nav .signup{border:2px solid var(--blue);border-radius:4px;padding:13px 22px;margin-left:14px}

/* hero */
.hero{height:685px;overflow:hidden}
.hero-photo{position:absolute;inset:0;background:linear-gradient(100deg,#121923 0%,#1f2a38 45%,#3a4048 75%,#262b32 100%)}
.hero-shade{position:absolute;inset:0;background:linear-gradient(90deg,rgba(10,14,24,.7),rgba(10,14,24,.15))}
.hero h1{position:absolute;left:112px;top:300px;color:var(--white);font-size:37px;font-weight:400;line-height:50px;text-transform:uppercase}
.hero .btn{position:absolute;left:112px;top:437px;width:145px;line-height:43px}
.scroll-down{position:absolute;left:554px;top:675px;width:92px;height:92px;border-radius:50%;background:var(--white);border:6px solid #eceff3;display:flex;align-items:center;justify-content:center;z-index:2}

/* about */
.about{height:589px}
.about-photo-back{left:180px;top:94px;width:360px;height:337px;border-radius:10px;background:linear-gradient(135deg,#8c8c8c,#4a4a4a 60%,#2a2a2a)}
.about-photo-front{left:112px;top:163px;width:362px;height:348px;border-radius:10px;background:linear-gradient(160deg,#2c2238,#12162a 60%,#2e2748)}
.about-frame{left:145px;top:128px;width:361px;height:346px;border:5px solid var(--blue);border-radius:12px}
.about-copy{left:605px;top:102px;width:483px}
.about-copy h2{font-size:34px;font-weight:500;line-height:42px;text-transform:uppercase;margin:18px 0 26px}
.step{margin-bottom:20px}
.step h4{font-size:16px;font-weight:500;display:flex;align-items:center;gap:20px;margin-bottom:12px}
.step h4::before{content:"»";color:var(--blue);font-size:17px}
.step p{font-size:13px;line-height:24px;color:var(--muted);padding-left:34px;text-align:justify}

/* widgets */
.widgets{height:1196px;background:linear-gradient(180deg,#121a2a,#0c1220);color:var(--white)}
.widgets .kicker{position:absolute;top:178px;width:100%}
.widgets .section-title{position:absolute;top:210px;width:100%}
.widget-grid{position:absolute;left:112px;top:344px;width:976px;display:grid;grid-template-columns:repeat(3,307px);column-gap:27px;row-gap:74px}
.widget-card{position:relative;height:248px;background:var(--card-dark);border-radius:3px;padding:80px 28px 0}
.widget-icon{position:absolute;left:28px;top:-40px;width:78px;height:78px;background:var(--blue);display:flex;align-items:center;justify-content:center}
.widget-card h3{font-size:18px;font-weight:500;text-transform:uppercase;margin-bottom:16px;white-space:nowrap}
.widget-card p{font-size:13px;line-height:23px;color:#cfd4dc;height:68px}
.learn{display:inline-block;margin-top:10px;color:var(--blue);font-size:12px;font-weight:700;text-transform:uppercase;text-decoration:none}
.widgets .btn{position:absolute;left:513px;top:965px;width:172px}

/* blog */
.blog{height:673px}
.blog .kicker{position:absolute;top:40px;width:100%}
.blog .section-title{position:absolute;top:72px;width:100%}
.post{position:absolute;background:var(--white);box-shadow:0 2px 14px rgba(0,0,0,.12)}
.post-lead{left:112px;top:140px;width:478px;height:446px;padding:9px}
.post-lead .post-photo{height:283px;background:linear-gradient(130deg,#cfc8bd,#7d7a74 50%,#3a3f48)}
.post-side{left:608px;width:480px;height:214px;padding:9px;display:flex}
.post-side .post-photo{width:197px;height:196px;flex:none}
.post-body{padding:22px 20px 0}
.post-side .post-body{padding:22px 12px 0 22px}
.date{display:flex;align-items:center;gap:10px;font-size:11px;color:#555}
.date i{width:22px;height:22px;border-radius:50%;background:var(--blue);display:inline-block}
.post h3{font-size:16px;font-weight:500;line-height:24px;text-transform:uppercase;margin:10px 0 8px}
.post p{font-size:13px;line-height:24px;color:var(--muted);text-align:justify}
.post .learn{margin-top:4px}

/* countdown */
.cta{height:670px;background:linear-gradient(180deg,#101726,#0b111c);color:var(--white)}
.cta .kicker{position:absolute;top:147px;width:100%}
.cta .section-title{position:absolute;top:180px;width:100%}
.countdown{position:absolute;left:219px;top:268px;display:flex;align-items:center;gap:0}
.unit{width:164px;height:162px;background:var(--card-dark);border-radius:4px;text-align:center;padding-top:22px}
.unit b{display:block;font-family:"Rubik",sans-serif;font-size:78px;font-weight:500;line-height:84px}
.unit span{color:var(--blue);font-size:19px}
.sep{width:36px;text-align:center;font-size:40px;font-weight:500}
.cta .btn{position:absolute;left:513px;top:473px;width:172px}

/* contact */
.contact{height:493px}
.contact .kicker{position:absolute;top:80px;width:100%}
.contact .section-title{position:absolute;top:120px;width:100%}
.contact-form{position:absolute;left:166px;top:199px;width:868px}
.field{background:var(--white);border:1px solid #eceef1;box-shadow:0 1px 8px rgba(0,0,0,.08);font-size:13px;color:#555;padding:0 16px;line-height:47px}
.row{display:flex;gap:11px;margin-bottom:13px}
.row .field{flex:1}
.field.message{height:93px;line-height:20px;padding-top:16px}
.contact .btn{position:absolute;left:523px;top:369px;width:154px}

/* footer */
.site-footer{height:393px;background:var(--navy);color:var(--white)}
.foot-logo{left:112px;top:242px;font-size:26px}
.foot-col{top:156px}
.foot-col h4{font-size:16px;font-weight:500;text-transform:uppercase;margin-bottom:22px}
.foot-col li{list-style:none;font-size:13px;margin-bottom:18px;display:flex;gap:24px}
.foot-col li::before{content:"»";color:var(--blue)}
.newsletter{display:flex;width:284px;height:46px;border:2px solid var(--white);border-radius:3px;background:var(--white);margin-bottom:16px}
.newsletter span{flex:1;color:#555;font-size:13px;line-height:42px;padding-left:16px}
.newsletter b{background:var(--blue);width:106px;font-size:13px;font-weight:500;line-height:42px;text-align:center;text-transform:uppercase}
.socials{display:flex;gap:8px}
.socials i{width:35px;height:35px;border-radius:50%;background:var(--white)}
.socials i:first-child{background:var(--blue)}
.foot-rule{left:112px;top:335px;width:976px;height:1px;background:rgba(255,255,255,.15)}
.copyright{top:354px;width:100%;text-align:center;font-size:12px}
.copyright em{font-style:normal;color:var(--blue)}
.page-code{right:50px;top:358px;font-size:9px;color:#9aa0aa}
</style>
</head>
<body>

<header class="site-header">
  <a class="logo" href="#"><span class="logo-mark"></span>QuillPatchery</a>
  <nav class="nav">
    <a class="active" href="#">Home</a>
    <a href="#">Widgets</a>
    <a href="#">Widget Information</a>
    <a href="#">Pricing</a>
    <svg width="16" height="16" viewBox="0 0 16 16" aria-label="Search"><circle cx="6.5" cy="6.5" r="4.8" fill="none" stroke="#fff" stroke-width="2"/><path d="M10 10l4.5 4.5" stroke="#fff" stroke-width="2"/></svg>
    <a class="signup" href="#">Sign Up</a>
  </nav>
</header>

<section class="hero">
  <div class="hero-photo" role="img" aria-label="Photo of a woman working on a laptop at a desk beside a glowing lamp"></div>
  <div class="hero-shade"></div>
  <h1>QuillPatchery Makes<br>Anything Possible</h1>
  <a class="btn" href="#">Get Started</a>
  <svg class="slant" style="bottom:0" height="130" viewBox="0 0 1200 130" preserveAspectRatio="none">
    <polygon points="256,130 1200,22 1200,130" fill="var(--grey-band)"/>
    <polygon points="0,130 1200,48 1200,130" fill="#fff"/>
    <polygon points="780,130 1200,10 1200,130" fill="var(--blue)"/>
    <polygon points="780,130 1200,60 1200,130" fill="var(--blue)"/>
  </svg>
</section>
<div class="scroll-down">
  <svg width="28" height="34" viewBox="0 0 28 34"><path d="M14 3v27M4 20l10 10 10-10" fill="none" stroke="var(--blue)" stroke-width="3" stroke-linecap="round"/></svg>
</div>

<section class="about">
  <div class="abs about-photo-back" role="img" aria-label="Photo of a person wearing glasses"></div>
  <div class="abs about-photo-front" role="img" aria-label="Photo of eyeglasses on a table with city lights behind"></div>
  <div class="abs about-frame"></div>
  <div class="abs about-copy">
    <p class="kicker">About Us</p>
    <h2>Welcome to<br>QuillPatchery</h2>
    <div class="step"><h4>BEFORE</h4><p>With LumaSite you can easily create stunning websites just by dragging and dropping.</p></div>
    <div class="step"><h4>NOW</h4><p>Use our library of advanced widgets to add everything from image galleries, slide shows, e-commerce stores</p></div>
    <div class="step"><h4>NEXT</h4><p>We don't plan to stop there, more widgets are on their way! Let us know if there are any widgets you need!</p></div>
  </div>
</section>

<section class="widgets">
  <svg class="slant" style="top:0" height="130" viewBox="0 0 1200 130" preserveAspectRatio="none">
    <polygon points="0,0 1200,0 1200,0 0,128" fill="#fff"/>
    <polygon points="0,112 943,0 943,12 0,130" fill="var(--grey-band)"/>
    <polygon points="0,0 420,52 0,100" fill="var(--blue)"/>
  </svg>
  <p class="kicker center">What We Do</p>
  <h2 class="section-title">Our Widgets</h2>
  <div class="widget-grid">
    <article class="widget-card">
      <div class="widget-icon"><svg width="44" height="44" viewBox="0 0 44 44" fill="none" stroke="#0e1422" stroke-width="2"><rect x="3" y="5" width="38" height="34" rx="2"/><path d="M3 13h38M9 20h10M9 26h10M9 32h10M24 20h11M24 26h11M24 32h11"/></svg></div>
      <h3>Navigation Bar</h3>
      <p>You certainly want to have more than just a single version of the Navigation Menu for the website</p>
      <a class="learn" href="#">Learn More &nbsp;»</a>
    </article>
    <article class="widget-card">
      <div class="widget-icon"><svg width="44" height="44" viewBox="0 0 44 44" fill="none" stroke="#0e1422" stroke-width="2"><rect x="3" y="6" width="38" height="26" rx="2"/><path d="M18 13l9 6-9 6z M14 38h16M22 32v6"/></svg></div>
      <h3>Reelio Video Gallery</h3>
      <p>Easy to use customizable video gallery for your Reelio videos.</p>
      <a class="learn" href="#">Learn More &nbsp;»</a>
    </article>
    <article class="widget-card">
      <div class="widget-icon"><svg width="44" height="44" viewBox="0 0 44 44" fill="none" stroke="#0e1422" stroke-width="2"><rect x="3" y="5" width="38" height="34" rx="2"/><rect x="9" y="11" width="26" height="22"/><path d="M9 30l8-8 6 6 4-4 8 8"/><circle cx="28" cy="17" r="2.5"/></svg></div>
      <h3>3D Image Gallery</h3>
      <p>Modern looking 3D image gallery to enhance your website.</p>
      <a class="learn" href="#">Learn More &nbsp;»</a>
    </article>
    <article class="widget-card">
      <div class="widget-icon"><svg width="44" height="44" viewBox="0 0 44 44" fill="none" stroke="#0e1422" stroke-width="2"><rect x="3" y="12" width="38" height="27" rx="2"/><path d="M3 20h38M9 27h16M9 32h10"/><path d="M26 10a6 6 0 0 1 12 0v4H26z"/></svg></div>
      <h3>Website Notification</h3>
      <p>Add a customizable modern looking notification to your site.</p>
      <a class="learn" href="#">Learn More &nbsp;»</a>
    </article>
    <article class="widget-card">
      <div class="widget-icon"><svg width="46" height="46" viewBox="0 0 46 46" fill="none" stroke="#0e1422" stroke-width="2.4"><circle cx="23" cy="23" r="19"/><circle cx="23" cy="23" r="13"/><path d="M17 18l6 6 6-6M17 24l6 6 6-6"/></svg></div>
      <h3>Scrollable List</h3>
      <p>Create multiple paragraphs with text wrapped around images.</p>
      <a class="learn" href="#">Learn More &nbsp;»</a>
    </article>
    <article class="widget-card">
      <div class="widget-icon"><svg width="44" height="44" viewBox="0 0 44 44" fill="none" stroke="#0e1422" stroke-width="2"><rect x="3" y="4" width="38" height="36" rx="2"/><rect x="9" y="10" width="13" height="12"/><path d="M26 11h10M26 16h10M26 21h10M9 28h27M9 33h27"/></svg></div>
      <h3>Advanced Image Wrap</h3>
      <p>Create multiple paragraphs with text wrapped around images.</p>
      <a class="learn" href="#">Learn More &nbsp;»</a>
    </article>
  </div>
  <a class="btn" href="#">View All Widgets</a>
  <svg class="slant" style="bottom:0" height="130" viewBox="0 0 1200 130" preserveAspectRatio="none">
    <polygon points="256,130 1200,22 1200,130" fill="var(--grey-band)"/>
    <polygon points="0,130 1200,48 1200,130" fill="#fff"/>
    <polygon points="780,130 1200,10 1200,130" fill="var(--blue)"/>
    <polygon points="780,130 1200,60 1200,130" fill="var(--blue)"/>
  </svg>
</section>

<section class="blog">
  <p class="kicker center">Blog</p>
  <h2 class="section-title">Latest News</h2>
  <article class="post post-lead">
    <div class="post-photo" role="img" aria-label="Photo of a team working together on laptops in an office"></div>
    <div class="post-body">
      <p class="date"><i></i>29 OCT 2020</p>
      <h3>LumaSite 3.4 and QuillPatchery<br>widgets compatibility</h3>
      <a class="learn" href="#">Read More &nbsp;»</a>
    </div>
  </article>
  <article class="post post-side" style="top:140px">
    <div class="post-photo" role="img" aria-label="Photo of an online shop displayed on a desktop monitor" style="background:linear-gradient(135deg,#d7d8dc,#8f96a3 60%,#5b6270)"></div>
    <div class="post-body">
      <p class="date"><i></i>15 JAN 2021</p>
      <h3>E-commerce options for LumaSite websites</h3>
      <p>In today's world, selling online is becoming the norm...</p>
      <a class="learn" href="#">Read More &nbsp;»</a>
    </div>
  </article>
  <article class="post post-side" style="top:372px">
    <div class="post-photo" role="img" aria-label="Illustration of a laptop showing an email popup" style="background:linear-gradient(135deg,#f1f3f6,#c9d2de 55%,#6f7c90)"></div>
    <div class="post-body">
      <p class="date"><i></i>27 SEP 2020</p>
      <h3>Visitor offers with popup &amp; slide out dialogs</h3>
      <p>When someone visits your website, you have only a few moments...</p>
      <a class="learn" href="#">Read More &nbsp;»</a>
    </div>
  </article>
</section>

<section class="cta">
  <svg class="slant" style="top:0" height="130" viewBox="0 0 1200 130" preserveAspectRatio="none">
    <polygon points="0,0 1200,0 1200,0 0,128" fill="#fff"/>
    <polygon points="0,112 943,0 943,12 0,130" fill="var(--grey-band)"/>
    <polygon points="0,0 420,52 0,100" fill="var(--blue)"/>
  </svg>
  <p class="kicker center">Ready to Start</p>
  <h2 class="section-title">Get Ready to Start?</h2>
  <div class="countdown">
    <div class="unit"><b>32</b><span>Days</span></div><div class="sep">:</div>
    <div class="unit"><b>07</b><span>Hours</span></div><div class="sep">:</div>
    <div class="unit"><b>44</b><span>Minutes</span></div><div class="sep">:</div>
    <div class="unit"><b>23</b><span>Seconds</span></div>
  </div>
  <a class="btn" href="#">Sign Up for Free</a>
  <svg class="slant" style="bottom:0" height="130" viewBox="0 0 1200 130" preserveAspectRatio="none">
    <polygon points="256,130 1200,22 1200,130" fill="var(--grey-band)"/>
    <polygon points="0,130 1200,48 1200,130" fill="#fff"/>
    <polygon points="780,130 1200,10 1200,130" fill="var(--blue)"/>
    <polygon points="780,130 1200,60 1200,130" fill="var(--blue)"/>
  </svg>
</section>

<section class="contact">
  <p class="kicker center">Contact Us</p>
  <h2 class="section-title">Get in Touch</h2>
  <form class="contact-form">
    <div class="row">
      <div class="field">Full Name</div>
      <div class="field">Phone</div>
      <div class="field">Email Address</div>
    </div>
    <div class="field message">Message</div>
  </form>
  <a class="btn" href="#">Send Message</a>
</section>

<footer class="site-footer">
  <svg class="slant" style="top:0" height="110" viewBox="0 0 1200 110" preserveAspectRatio="none">
    <polygon points="0,0 1200,0 1200,0 0,108" fill="#fff"/>
    <polygon points="0,94 943,0 943,12 0,112" fill="var(--grey-band)"/>
    <polygon points="0,0 420,48 0,86" fill="var(--blue)"/>
  </svg>
  <a class="logo abs foot-logo" href="#"><span class="logo-mark"></span>QuillPatchery</a>
  <div class="abs foot-col" style="left:396px">
    <h4>Navigation</h4>
    <ul><li>Home</li><li>Widgets</li><li>Widget Information</li><li>Pricing</li></ul>
  </div>
  <div class="abs foot-col" style="left:614px">
    <h4>Quick Links</h4>
    <ul><li>FAQ</li><li>Privacy Policy</li><li>Terms Of Use</li></ul>
  </div>
  <div class="abs foot-col" style="left:804px">
    <h4>Newsletter Signup</h4>
    <div class="newsletter"><span>Email Address</span><b>Sign Up</b></div>
    <div class="socials"><i></i><i></i><i></i></div>
  </div>
  <div class="abs foot-rule"></div>
  <p class="abs copyright">© 2022 <em>QuillPatchery</em> &nbsp;| &nbsp;All Rights Reserved</p>
  <p class="abs page-code">C45</p>
</footer>

</body>
</html>
```